Design a Website for an IT Support Company

We are an IT support company that provides commercial IT support and services to small and medium sized businesses. We are in need of a website to be developed for our business.
We would like to work with someone who is either familiar with the IT field, or has developed a website for an IT support company in the past.
Some examples of designs/layouts that we like:
https://www.veldaworks.example/
http://www.marsbyquill.example/
http://817kq.example/
http://www.olbenstructures.example/
http://www.bykq.example/
I have attached a word document that gives a menu system/page layout format that we would like for our website as well as branch office phone numbers. Our logo is also attached that you can use for your design purposes. We currently do not have copy produced for all of the pages outlined in the word document, but would get this done during the project with the selected designer.
We would like the website to be SEO friendly & fully responsive. We would prefer a Wordpress format, however, we are open to HTML formats as well.

```html
<!DOCTYPE html>
<html lang="en">
<head>
<meta charset="utf-8">
<title>Vantora IT – Commercial IT Support</title>
<link rel="stylesheet" href="https://fonts.googleapis.com/css2?family=Jura:wght@400;500;600&family=Open+Sans:ital,wght@0,400;0,600;0,700;1,400&display=swap">
<style>
:root{
  --blue:#0b6fbf;
  --blue-deep:#085a9e;
  --blue-light:#2e8fdc;
  --ink:#222;
  --muted:#777;
  --nav-top:#3a3d40;
  --nav-bottom:#17191b;
  --footer-top:#3a3a3a;
  --footer-bottom:#111;
  --white:#fff;
}
*{margin:0;padding:0;box-sizing:border-box}
html,body{width:1200px;height:3186px;overflow:hidden;background:var(--white)}
body{position:relative;font-family:"Open Sans",Arial,sans-serif;color:var(--ink)}
.abs{position:absolute}
.display{font-family:"Jura","Open Sans",sans-serif}

/* header */
.site-header{left:0;top:0;width:1200px;height:106px;background:var(--white)}
.brand{left:78px;top:26px;display:flex;align-items:center;gap:12px}
.brand-dot{width:44px;height:44px;border-radius:50%;background:var(--blue)}
.brand-name{font-family:"Jura",sans-serif;font-weight:600;font-size:34px;color:#1a1a1a}
.call{left:856px;top:24px;display:flex;gap:14px;align-items:center}
.call-label{font-size:15px;font-weight:700;color:#222}
.call-number{font-size:30px;font-weight:600;color:var(--blue);line-height:1.1}

/* nav */
.main-nav{left:0;top:106px;width:1200px;height:64px;background:linear-gradient(var(--nav-top),var(--nav-bottom));border-bottom:3px solid var(--blue)}
.nav-item{top:0;height:61px;display:flex;align-items:center;gap:9px;color:var(--white);font-size:15px;text-transform:uppercase}
.nav-item .pip{width:8px;height:8px;border-radius:50%;background:var(--blue-light)}
.nav-item.active{background:var(--blue);top:6px;height:55px;padding:0 16px}
.nav-sep{top:10px;width:1px;height:44px;background:#555}
.search{left:860px;top:0;width:340px;height:61px;display:flex;align-items:center;justify-content:space-between;padding:0 20px;color:#9a9a9a;font-size:16px;border-left:1px solid #555}

/* hero */
.hero{left:0;top:170px;width:1200px;height:512px;background:linear-gradient(100deg,#8fc6e8 0%,#4a95c9 40%,#1d5f93 75%,#0c3c66 100%)}
.hero-title{left:80px;top:108px;font-family:"Open Sans",sans-serif;font-weight:700;font-size:54px;line-height:62px;color:var(--white);text-transform:uppercase}
.hero-sub{left:80px;top:250px;font-style:italic;font-size:17px;line-height:30px;color:var(--white)}
.btn{display:flex;align-items:center;justify-content:center;background:var(--blue);color:var(--white);border-radius:6px;font-family:"Jura",sans-serif;font-weight:600;text-transform:uppercase}
.hero-btn{left:79px;top:323px;width:206px;height:54px;font-size:24px}
.hero-arrow{left:28px;top:205px}
.dots{left:548px;top:476px;display:flex;gap:12px}
.dots span{width:15px;height:15px;border-radius:50%;border:2px solid #2a78b8}
.dots span.on{background:#2a78b8}

/* welcome */
.welcome-title{left:0;top:725px;width:1200px;text-align:center;font-size:48px;color:#222;display:flex;justify-content:center;align-items:center;gap:16px}
.welcome-title em{font-style:normal;color:var(--blue)}
.welcome-title .mark{width:22px;height:22px;border-radius:50%;background:var(--blue)}
.welcome-copy{left:150px;top:800px;width:900px;text-align:center;font-size:13.5px;line-height:28px;color:var(--muted)}
.welcome-copy p+p{margin-top:6px}
.more-btn{left:503px;top:958px;width:192px;height:55px;font-size:24px}

/* service bands */
.band{left:0;width:1200px}
.band svg{position:absolute;left:0;top:0}
.service-title{font-family:"Jura",sans-serif;font-size:36px;letter-spacing:2px;text-transform:uppercase}
.service-list{list-style:none;font-size:15px;line-height:29px}
.service-list li{display:flex;align-items:center;gap:16px}
.service-list li::before{content:"";width:9px;height:9px;border-radius:50%;background:currentColor;opacity:.85}
.data{top:1075px;height:448px}
.data .service-title{left:77px;top:42px;color:var(--white)}
.data .service-list{left:77px;top:92px;color:var(--white)}
.cloud{top:1523px;height:406px}
.cloud .service-title{left:648px;top:86px;color:var(--blue)}
.cloud .service-list{left:648px;top:145px;color:#666}
.cloud .service-list li::before{background:var(--blue)}
.voice{top:1929px;height:450px}
.voice .service-title{right:79px;top:112px;color:var(--white)}
.voice .service-list{right:79px;top:175px;color:var(--white);text-align:right}
.voice .service-list li{flex-direction:row-reverse}

/* contact */
.contact{top:2379px;height:451px}
.contact-title{left:0;top:55px;width:1200px;text-align:center;font-size:48px;color:var(--blue)}
.contact-copy{left:200px;top:122px;width:800px;text-align:center;font-size:14px;line-height:28px;color:#666}
.office{display:flex;align-items:center;gap:18px}
.office .ring{width:52px;height:52px;border-radius:50%;background:var(--blue);display:flex;align-items:center;justify-content:center}
.office-city{font-size:14px;font-weight:700;color:#222}
.office-phone{font-size:25px;color:var(--blue);line-height:1.15}

/* footer */
.site-footer{left:0;top:2830px;width:1200px;height:292px;background:linear-gradient(var(--footer-top),var(--footer-bottom));border-top:4px solid var(--blue)}
.footer-heading{font-family:"Jura",sans-serif;font-size:21px;font-weight:600;color:var(--blue-light)}
.footer-text{font-size:14px;line-height:27px;color:#bdbdbd}
.footer-link{color:var(--blue-light);text-decoration:underline}
.sitemap{list-style:none;font-size:14px;line-height:32px;color:#bdbdbd}
.sitemap li{display:flex;align-items:center;gap:18px}
.sitemap li::before{content:"";width:8px;height:8px;border-radius:50%;background:#bbb}
.email-field{left:811px;top:158px;width:310px;height:46px;background:#f1f1f1;font-size:14px;color:#666;display:flex;align-items:center;padding-left:14px}
.subscribe{left:811px;top:210px;width:166px;height:46px;font-size:19px;border-radius:4px}
.copyright{left:0;top:3122px;width:1200px;height:64px;background:var(--blue);color:#e5f1fb;font-size:13px;display:flex;align-items:center;justify-content:center}
</style>
</head>
<body>

<header class="site-header abs">
  <div class="brand abs"><span class="brand-dot"></span><span class="brand-name">Vantora IT</span></div>
  <div class="call abs">
    <svg width="50" height="50" viewBox="0 0 24 24"><path fill="#0b6fbf" d="M6.6 10.8a15.1 15.1 0 0 0 6.6 6.6l2.2-2.2c.3-.3.7-.4 1-.2 1.1.4 2.3.6 3.6.6.6 0 1 .4 1 1V20c0 .6-.4 1-1 1C10.6 21 3 13.4 3 4c0-.6.4-1 1-1h3.5c.6 0 1 .4 1 1 0 1.3.2 2.5.6 3.6.1.3 0 .7-.2 1z"/></svg>
    <div><div class="call-label">Call Us On :</div><div class="call-number">972-555-0140</div></div>
  </div>
</header>

<nav class="main-nav abs">
  <div class="nav-item active abs" style="left:77px"><span class="pip"></span>Home</div>
  <div class="nav-sep abs" style="left:338px"></div>
  <div class="nav-item abs" style="left:208px"><span class="pip"></span>About Us</div>
  <div class="nav-item abs" style="left:358px"><span class="pip"></span>Services</div>
  <div class="nav-sep abs" style="left:490px"></div>
  <div class="nav-item abs" style="left:510px"><span class="pip"></span>Why Vantora IT</div>
  <div class="nav-sep abs" style="left:700px"></div>
  <div class="nav-item abs" style="left:722px"><span class="pip"></span>Contact</div>
  <div class="search abs">Search....
    <svg width="22" height="22" viewBox="0 0 24 24"><circle cx="10" cy="10" r="7" fill="none" stroke="#bbb" stroke-width="3"/><path d="M15 15l6 6" stroke="#bbb" stroke-width="3"/></svg>
  </div>
</nav>

<section class="hero abs" role="img" aria-label="Businessman touching a glowing analytics dashboard with charts">
  <svg class="hero-arrow abs" width="20" height="60" viewBox="0 0 20 60"><path d="M18 2L2 30l16 28" fill="none" stroke="#fff" stroke-width="2"/></svg>
  <h1 class="hero-title abs">Get More From Your<br>Technology</h1>
  <p class="hero-sub abs">Provides Commercial It Support And Services To Small &amp; Medium Sized<br>Businesses on Vantora It.</p>
  <a class="btn hero-btn abs">Contact Us</a>
  <div class="dots abs"><span></span><span></span><span class="on"></span><span></span></div>
</section>

<section class="welcome">
  <h2 class="welcome-title display abs"><span class="mark"></span>Welcome to <em>Vantora It</em></h2>
  <div class="welcome-copy abs">
    <p>Lorem Ipsum is simply dummy text of the printing and typesetting industry. Lorem Ipsum has been the industry's standard dummy text<br>ever since the 1500s, when an unknown printer took a galley of type and scrambled.</p>
    <p>Lorem Ipsum is simply dummy text of the printing and typesetting industry. Lorem Ipsum has been the industry's standard dummy text ever since the 1500s, when an unknown printer took a galley of type and scrambled it to make a type specimen book. It has survived not only five centuries, but also the leap into electronic typesetting, remaining essentially unchanged.</p>
  </div>
  <a class="btn more-btn abs">Know More</a>
</section>

<section class="band data abs">
  <svg width="1200" height="448" viewBox="0 0 1200 448">
    <defs><linearGradient id="dataGlow" x1="0" y1="0" x2="1" y2="1"><stop offset="0" stop-color="#1c3f9a"/><stop offset=".5" stop-color="#3c6fe0"/><stop offset="1" stop-color="#0a1a55"/></linearGradient></defs>
    <rect width="1200" height="448" fill="#0b6fbf"/>
    <polygon points="672,0 1200,0 1200,448 498,448" fill="#fff"/>
    <polygon points="686,0 1200,0 1200,448 512,448" fill="url(#dataGlow)" role="img" aria-label="Hands holding a glowing holographic data display"/>
  </svg>
  <h3 class="service-title abs">Data</h3>
  <ul class="service-list abs">
    <li>Managed It Services</li><li>It Support &amp; Consulting</li><li>It Helpdesk Services</li><li>Network Security</li><li>Data Backup &amp; Recovery</li><li>Servers &amp; Virtualization</li><li>Remote Monitoring Services</li><li>Wireless Networking</li><li>Email &amp; Spam Threat</li><li>Management</li><li>Structured Cabling</li>
  </ul>
</section>

<section class="band cloud abs">
  <svg width="660" height="406" viewBox="0 0 660 406">
    <defs><radialGradient id="cloudSketch" cx=".45" cy=".45" r=".6"><stop offset="0" stop-color="#cfe2ef"/><stop offset=".6" stop-color="#eef2f4"/><stop offset="1" stop-color="#fff"/></radialGradient></defs>
    <rect x="170" y="0" width="430" height="406" fill="url(#cloudSketch)" role="img" aria-label="Hand sketching a cloud connected to computers and devices"/>
  </svg>
  <h3 class="service-title abs">Cloud</h3>
  <ul class="service-list abs">
    <li>Suitework 365 Migrations</li><li>Nimbus Cloud Management Services</li><li>Cloud Migration Services</li><li>Hosted Virtual Servers</li><li>Hosted Telephone Systems</li>
  </ul>
</section>

<section class="band voice abs">
  <svg width="1200" height="450" viewBox="0 0 1200 450">
    <defs><linearGradient id="voiceGlow" x1="0" y1="0" x2="1" y2="0"><stop offset="0" stop-color="#02071a"/><stop offset=".45" stop-color="#14348a"/><stop offset="1" stop-color="#3f7fe6"/></linearGradient></defs>
    <rect width="1200" height="450" fill="#0b6fbf"/>
    <polygon points="0,0 496,0 676,450 0,450" fill="#fff"/>
    <polygon points="0,0 482,0 662,450 0,450" fill="url(#voiceGlow)" role="img" aria-label="Silhouette in profile with a glowing sound wave"/>
  </svg>
  <h3 class="service-title abs">Voice</h3>
  <ul class="service-list abs">
    <li>Astrel Consulting</li><li>Business Telephone Systems</li><li>Multiple Office Phone Systems</li><li>Granvale Telephone Systems</li><li>SIP Trunks</li>
  </ul>
</section>

<section class="band contact abs">
  <h2 class="contact-title display abs">Contact Us On</h2>
  <p class="contact-copy abs">Lorem Ipsum is simply dummy text of the printing and typesetting industry. Lorem Ipsum has been the industry's standard dummy text ever since the 1500s, when an unknown printer took</p>

  <div class="office abs" style="left:350px;top:195px"><span class="ring"><svg width="24" height="24" viewBox="0 0 24 24"><path fill="#fff" d="M6.6 10.8a15.1 15.1 0 0 0 6.6 6.6l2.2-2.2c.3-.3.7-.4 1-.2 1.1.4 2.3.6 3.6.6.6 0 1 .4 1 1V20c0 .6-.4 1-1 1C10.6 21 3 13.4 3 4c0-.6.4-1 1-1h3.5c.6 0 1 .4 1 1 0 1.3.2 2.5.6 3.6.1.3 0 .7-.2 1z"/></svg></span><div><div class="office-city">Main Number :</div><div class="office-phone">972-555-0140</div></div></div>
  <div class="office abs" style="left:620px;top:195px"><span class="ring"><svg width="24" height="24" viewBox="0 0 24 24"><path fill="#fff" d="M6.6 10.8a15.1 15.1 0 0 0 6.6 6.6l2.2-2.2c.3-.3.7-.4 1-.2 1.1.4 2.3.6 3.6.6.6 0 1 .4 1 1V20c0 .6-.4 1-1 1C10.6 21 3 13.4 3 4c0-.6.4-1 1-1h3.5c.6 0 1 .4 1 1 0 1.3.2 2.5.6 3.6.1.3 0 .7-.2 1z"/></svg></span><div><div class="office-city">Austin :</div><div class="office-phone">512-555-0193</div></div></div>
  <div class="office abs" style="left:350px;top:263px"><span class="ring"><svg width="24" height="24" viewBox="0 0 24 24"><path fill="#fff" d="M6.6 10.8a15.1 15.1 0 0 0 6.6 6.6l2.2-2.2c.3-.3.7-.4 1-.2 1.1.4 2.3.6 3.6.6.6 0 1 .4 1 1V20c0 .6-.4 1-1 1C10.6 21 3 13.4 3 4c0-.6.4-1 1-1h3.5c.6 0 1 .4 1 1 0 1.3.2 2.5.6 3.6.1.3 0 .7-.2 1z"/></svg></span><div><div class="office-city">Houston :</div><div class="office-phone">832-555-0172</div></div></div>
  <div class="office abs" style="left:620px;top:263px"><span class="ring"><svg width="24" height="24" viewBox="0 0 24 24"><path fill="#fff" d="M6.6 10.8a15.1 15.1 0 0 0 6.6 6.6l2.2-2.2c.3-.3.7-.4 1-.2 1.1.4 2.3.6 3.6.6.6 0 1 .4 1 1V20c0 .6-.4 1-1 1C10.6 21 3 13.4 3 4c0-.6.4-1 1-1h3.5c.6 0 1 .4 1 1 0 1.3.2 2.5.6 3.6.1.3 0 .7-.2 1z"/></svg></span><div><div class="office-city">Tulsa :</div><div class="office-phone">918-555-0127</div></div></div>
  <div class="office abs" style="left:350px;top:331px"><span class="ring"><svg width="24" height="24" viewBox="0 0 24 24"><path fill="#fff" d="M6.6 10.8a15.1 15.1 0 0 0 6.6 6.6l2.2-2.2c.3-.3.7-.4 1-.2 1.1.4 2.3.6 3.6.6.6 0 1 .4 1 1V20c0 .6-.4 1-1 1C10.6 21 3 13.4 3 4c0-.6.4-1 1-1h3.5c.6 0 1 .4 1 1 0 1.3.2 2.5.6 3.6.1.3 0 .7-.2 1z"/></svg></span><div><div class="office-city">San Antonio :</div><div class="office-phone">210-555-0118</div></div></div>
  <div class="office abs" style="left:620px;top:331px"><span class="ring"><svg width="24" height="24" viewBox="0 0 24 24"><path fill="#fff" d="M6.6 10.8a15.1 15.1 0 0 0 6.6 6.6l2.2-2.2c.3-.3.7-.4 1-.2 1.1.4 2.3.6 3.6.6.6 0 1 .4 1 1V20c0 .6-.4 1-1 1C10.6 21 3 13.4 3 4c0-.6.4-1 1-1h3.5c.6 0 1 .4 1 1 0 1.3.2 2.5.6 3.6.1.3 0 .7-.2 1z"/></svg></span><div><div class="office-city">Oklahoma City :</div><div class="office-phone">405-555-0164</div></div></div>
</section>

<footer class="site-footer abs">
  <h4 class="footer-heading abs" style="left:79px;top:32px">About Us</h4>
  <p class="footer-text abs" style="left:79px;top:76px;width:300px">Lorem Ipsum is simply dummy text of the printing and typesetting industry. Lorem Ipsum has been the industry's standard dummy text ever since the, when an unk nown printer took a galley of type.</p>
  <a class="footer-text footer-link abs" style="left:79px;top:222px">Read More...</a>

  <h4 class="footer-heading abs" style="left:446px;top:32px">Sitemap</h4>
  <ul class="sitemap abs" style="left:446px;top:76px">
    <li>Home</li><li>About Us</li><li>Services</li><li>Why Vantora IT</li><li>Contact Us</li>
  </ul>

  <h4 class="footer-heading abs" style="left:811px;top:32px">Newsletter</h4>
  <p class="footer-text abs" style="left:811px;top:76px;width:340px">Would you like to receive exclusive access to articles, white papers and our regular monthly newsletter?</p>
  <div class="email-field abs">Enter Email Id</div>
  <a class="btn subscribe abs">Subscribe</a>
</footer>

<div class="copyright abs">©Vantora IT- 2017 All Right Reserved</div>

</body>
</html>
```